Business Card Design & Gift cards, Gift Cert, Donation Card

Retail Gift Store-in addition to Business Cards we'd like sequenced 2 sided Gift cards, Gift Certificate Cards, and Donation Cards.please see examples and email for clarificationlogos attached with examples-
Gift Card, Gift Certificate and Donation Card will all be same style just differant upper right title, with back side info as example.
business card, as example is single sided.
looking for additional ideas for layout

Industry/Entity Type

Business

Contact Information for Business Card

211 Newman St.East Tawas, MI 48730989.362.8730Office@BrewKrew.com

Requirements
Must have
• Blue as per example
• Logos provided
• like gradiant background

```html
<!DOCTYPE html>
<html lang="en">
<head>
<meta charset="utf-8">
<title>Tillow Marsh – Business Card</title>
<link rel="stylesheet" href="https://fonts.googleapis.com/css2?family=Delius&display=swap">
<style>
  :root {
    --page-bg: #e9e6e1;
    --sky-top: #7db6e3;
    --sky-bottom: #eef3f8;
    --band-blue: #0b2fc4;
    --ink-blue: #1f2fc0;
    --ink-dark: #141414;
    --sun-yellow: #f1dc2e;
  }
  * { box-sizing: border-box; margin: 0; padding: 0; }
  html, body { width: 1200px; height: 902px; overflow: hidden; }
  body {
    background: var(--page-bg);
    font-family: "Delius", "Comic Sans MS", cursive;
    position: relative;
  }
  .business-card {
    position: absolute;
    left: 100px;
    top: 165px;
    width: 1000px;
    height: 572px;
    border-radius: 6px;
    overflow: hidden;
    background: linear-gradient(180deg, var(--sky-top) 0%, #b6d4ee 45%, var(--sky-bottom) 80%);
    box-shadow: 0 10px 30px rgba(0,0,0,0.18);
  }
  .bottom-band {
    position: absolute;
    left: 0;
    right: 0;
    bottom: 0;
    height: 118px;
    background: var(--band-blue);
  }
  .brand-name {
    position: absolute;
    left: 80px;
    top: 92px;
    font-size: 58px;
    color: var(--ink-blue);
    letter-spacing: 1px;
    line-height: 1;
  }
  .mascot-art {
    position: absolute;
    left: 170px;
    top: 240px;
    width: 380px;
    height: 332px;
    background: linear-gradient(160deg, #3a52c9 0%, #5b78d6 50%, var(--sun-yellow) 100%);
    opacity: 0.85;
    border-radius: 4px;
  }
  .contact-list {
    position: absolute;
    right: 46px;
    top: 200px;
    list-style: none;
    text-align: right;
    color: var(--ink-dark);
    font-size: 29px;
    line-height: 44px;
  }
  .contact-list li { display: flex; justify-content: flex-end; align-items: center; gap: 18px; }
  .contact-icon {
    width: 24px;
    height: 24px;
    background: var(--ink-blue);
    border-radius: 3px;
    display: inline-flex;
    align-items: center;
    justify-content: center;
  }
  .contact-icon svg { width: 16px; height: 16px; }
  .icon-spacer { width: 24px; height: 24px; display: inline-block; }
</style>
</head>
<body>
  <div class="business-card">
    <div class="bottom-band"></div>
    <div class="brand-name">Tillow Marsh</div>
    <div class="mascot-art" role="img" aria-label="Playful blue stick-figure mascot striding over a yellow rising sun"></div>
    <ul class="contact-list">
      <li>989.517.4296
        <span class="contact-icon"><svg viewBox="0 0 16 16"><path d="M4 2l3 3-1.5 1.5a8 8 0 0 0 4 4L11 9l3 3-2 2C7 14 2 9 2 4z" fill="#fff"/></svg></span>
      </li>
      <li>Office@TillowMarsh.com
        <span class="contact-icon"><svg viewBox="0 0 16 16"><rect x="2" y="4" width="12" height="8" fill="none" stroke="#fff" stroke-width="1.5"/><path d="M2 4l6 5 6-5" fill="none" stroke="#fff" stroke-width="1.5"/></svg></span>
      </li>
      <li>482 Larkfield Ave.
        <span class="contact-icon"><svg viewBox="0 0 16 16"><path d="M8 2a4 4 0 0 0-4 4c0 3 4 8 4 8s4-5 4-8a4 4 0 0 0-4-4z" fill="#fff"/><circle cx="8" cy="6" r="1.5" fill="#1f2fc0"/></svg></span>
      </li>
      <li>Port Alder, MI 48762<span class="icon-spacer"></span></li>
    </ul>
  </div>
</body>
</html>
```